birchwell hollow cattle company website

we would like a home page, an about us page, a page for sires, a page for dams, A sale page where we can list progreny for sale and a contact us. on the about us page we would like there to be a family picture. on the sires page we would like to have a picture of each sire, a description beside them and a link to their online profile at northern hereford registry. on the dam page we would like to have a picture of each dam, aswell as a description beside them aswell as a link to the northern hereford registry site. would like the website to very mobile phone friendly as expecting most traffic to be on phone. we would like the website to look and feel very mich like a farm, rustic, barbed wire and other farm feels. we would also like a frozen genetics pages where we can include pictures and descriptions of the sires and dams aswell as a price for embryos and semen. we need to website to be easy to maintain so we can update pictures and information as it changes, we would like there to be a feature so that people can sign up to be on our mailing list by giving us their mailing addess and email and full name
aswell as an area where they can send us a message to contact us.

leaving for work for 3 weeks in the canadian arctic will have limited ability to use the internet

Target Market(s)

other ranchers, farmers, cattlemen,

Industry/Entity Type

farming, agriculture, cattle

Coding

Coded - Design and coding required

Requirements
Must have
• about page, contact page, sires page, dams page, SALE page.
Nice to have
• country/farm vibe, barbed wire, wood,

```html
<!DOCTYPE html>
<html lang="en">
<head>
<meta charset="utf-8">
<title>Birchwell Hollow Cattle Company – Home</title>
<link href="https://fonts.googleapis.com/css2?family=Bebas+Neue&family=Poppins:wght@400;500&display=swap" rel="stylesheet">
<style>
:root{
  --wood-dark:#3a2417;
  --wood-mid:#5a3a26;
  --brown:#5b3826;
  --brown-deep:#4a2c1e;
  --tan:#c9a06e;
  --tan-light:#e6cfa8;
  --cream:#f8f1e5;
  --cream-2:#f3eadb;
  --ink:#4a3a30;
  --text:#5a4a40;
  --footer:#2a211c;
  --white:#ffffff;
  --rust:#8a5236;
}
*{margin:0;padding:0;box-sizing:border-box}
html,body{width:1200px;height:3743px;overflow:hidden}
body{position:relative;background:var(--cream);font-family:'Poppins',sans-serif;color:var(--text)}
.abs{position:absolute}
.heading{font-family:'Bebas Neue',sans-serif;color:var(--brown-deep);letter-spacing:.5px;font-weight:400}
.wire{position:absolute;height:2px;width:64px;background:var(--brown)}
.btn{position:absolute;display:flex;align-items:center;justify-content:center;font-family:'Bebas Neue',sans-serif;letter-spacing:1px;color:var(--cream);background:var(--brown);border:2px solid var(--brown);box-shadow:inset 0 0 0 2px var(--cream),0 0 0 2px var(--brown);border-radius:3px;text-decoration:none}
.btn-tan{background:var(--tan);border-color:var(--tan);box-shadow:inset 0 0 0 2px var(--cream),0 0 0 2px var(--tan);color:var(--white)}

/* header */
.site-header{left:0;top:0;width:1200px;height:98px;background:linear-gradient(180deg,#4a2f1f,#36221a);border-bottom:2px solid #2a1a12}
.nav a{position:absolute;top:40px;font-size:13px;color:var(--white);text-decoration:none;letter-spacing:.3px}
.brand{left:526px;top:0;width:148px;height:165px;background:var(--wood-mid);border-radius:0 0 74px 74px;display:flex;align-items:flex-end;justify-content:center;padding-bottom:26px;border:2px solid #2a1a12;border-top:0;text-decoration:none}
.brand span{font-family:'Bebas Neue',sans-serif;color:var(--cream);font-size:24px;line-height:24px;text-align:center;width:120px}

/* hero */
.hero{left:0;top:98px;width:1200px;height:622px;background:radial-gradient(ellipse at 55% 45%,#7a4028 0%,#5c3a28 35%,#6b6a66 70%,#8a7a5e 100%)}
.hero-title{left:0;width:1200px;top:428px;text-align:center;font-size:82px;color:var(--white);text-shadow:0 3px 8px rgba(0,0,0,.35)}
.hero-sub{left:0;width:1200px;top:527px;text-align:center;font-size:26px;color:var(--white);letter-spacing:1px}

/* about */
.photo{position:absolute;border:6px solid var(--tan-light);box-shadow:0 6px 12px rgba(0,0,0,.25)}
.about-text{left:668px;top:925px;width:400px;font-size:12.5px;line-height:23px}

/* features */
.features{left:0;top:1235px;width:1200px;height:427px;background:var(--cream-2)}
.feature{position:absolute;top:1320px;width:300px;text-align:center}
.feature .ring{width:140px;height:140px;margin:0 auto;border-radius:50%;border:4px solid var(--tan);padding:6px}
.feature .ring div{width:100%;height:100%;border-radius:50%;background:var(--brown-deep);display:flex;align-items:center;justify-content:center}
.feature h3{font-family:'Bebas Neue',sans-serif;font-size:21px;color:var(--brown-deep);margin-top:20px;font-weight:400}
.feature p{font-size:12.5px;line-height:23px;margin:6px auto 0;width:250px}

/* services */
.card{position:absolute;top:1835px;width:285px;text-align:center}
.card .photo{position:relative;height:203px;width:285px}
.card h3{font-family:'Bebas Neue',sans-serif;font-size:24px;color:var(--brown-deep);margin-top:34px;font-weight:400}
.card p{font-size:12.5px;line-height:20px;margin-top:6px}

.field-band{left:0;top:2208px;width:1200px;height:287px;background:linear-gradient(180deg,#b8c8cc 0%,#a9b4a8 40%,#6b4a30 60%,#6c8a3a 78%,#5e7f2e 100%)}

/* forms */
.input{position:absolute;background:var(--white);border:1px solid #e3d8c8;border-radius:4px;font-size:11.5px;color:#8a7e74;display:flex;align-items:center;padding-left:16px}
.input svg{flex:none}
.input .sep{width:1px;height:18px;background:#d8cec2;margin:0 10px}
.input.top{align-items:flex-start;padding-top:14px}

.trail{left:0;top:3075px;width:1200px;height:278px;background:linear-gradient(90deg,#3a2518,#5a3c28 30%,#4a3020 60%,#5c3d29 85%,#3a2518)}
.footer{left:0;top:3353px;width:1200px;height:390px;background:var(--footer);color:var(--white)}
.footer h4{font-family:'Bebas Neue',sans-serif;font-size:19px;font-weight:400;color:var(--white)}
.footer .links a{display:block;color:var(--white);text-decoration:none;font-size:13px;line-height:26.5px}
.footer .contact{font-size:12px;line-height:19px}
.footer .social div{display:flex;align-items:center;gap:10px;font-size:13px;height:41px}
.footer .social i{width:30px;height:30px;border-radius:50%;border:2px solid var(--white);display:inline-block;position:relative}
.footer .social i::after{content:"";position:absolute;left:8px;top:8px;width:10px;height:10px;border-radius:50%;background:var(--white)}
</style>
</head>
<body>

<header class="abs site-header">
  <nav class="nav">
    <a style="left:71px">HOME</a>
    <a style="left:173px">ABOUT US</a>
    <a style="left:302px">SIRES</a>
    <a style="left:402px">DAMS</a>
    <a style="left:759px">FROZEN GENETICS</a>
    <a style="left:943px">SALE</a>
    <a style="left:1042px">CONTACT US</a>
  </nav>
</header>

<section class="abs hero" role="img" aria-label="Photo of a red bull standing on straw in a corral"></section>
<a class="brand abs"><span>Birchwell Hollow Cattle Company</span></a>
<h1 class="abs heading hero-title">Birchwell Hollow Ranch</h1>
<p class="abs heading hero-sub">Premium Black Angus • Seedstock • Frozen Genetics</p>
<a class="btn btn-tan" style="left:496px;top:583px;width:186px;height:36px;font-size:17px">• View Sales Offer •</a>

<!-- about -->
<div class="photo" style="left:141px;top:805px;width:463px;height:328px;background:linear-gradient(135deg,#6e5040,#4d3426 60%,#7a6a5a)" role="img" aria-label="Family photo in front of a wooden barn door"></div>
<h2 class="abs heading" style="left:667px;top:843px;font-size:42px">Birchwell Hollow Ranch</h2>
<div class="wire" style="left:668px;top:898px"></div>
<p class="abs about-text">Nestled in the heart of cattle country, our family has dedicated over 70 years to raising exceptional Black Angus cattle. We pride ourselves on superior genetics, sustainable ranching practices, and the honest, hard-working values that have defined our operation for generations.</p>
<a class="btn" style="left:669px;top:1062px;width:189px;height:40px;font-size:17px">• View Sales Offer •</a>

<!-- features -->
<section class="abs features"></section>
<div class="feature" style="left:118px">
  <div class="ring"><div><svg width="58" height="50" viewBox="0 0 58 50" fill="#fff"><rect x="4" y="30" width="12" height="18"/><rect x="23" y="16" width="12" height="32"/><rect x="42" y="4" width="12" height="44"/></svg></div></div>
  <h3>Superior Genetics</h3><p>Our breeding program focuses on proven bloodlines that deliver consistent quality and performance.</p></div>
<div class="feature" style="left:450px">
  <div class="ring"><div><svg width="58" height="46" viewBox="0 0 58 46" fill="none" stroke="#fff" stroke-width="8" stroke-linecap="round" stroke-linejoin="round"><path d="M6 24l15 15L52 7"/></svg></div></div>
  <h3>Registered Angus</h3><p>All our cattle are registered with the Northern Hereford Registry with complete documentation.</p></div>
<div class="feature" style="left:782px">
  <div class="ring"><div><svg width="60" height="54" viewBox="0 0 60 54" fill="#fff"><path d="M30 2L2 26h8v26h16V36h8v16h16V26h8z"/></svg></div></div>
  <h3>Family Values</h3><p>Three generations of experience and dedication to ethical, sustainable cattle ranching.</p></div>

<!-- services -->
<h2 class="abs heading" style="left:0;width:1200px;text-align:center;top:1740px;font-size:43px">Tradition &amp; Quality Since 1987</h2>
<div class="wire" style="left:568px;top:1799px"></div>
<div class="card" style="left:141px"><div class="photo" style="background:linear-gradient(135deg,#a8502a,#7a3a1e 60%,#c8782e)" role="img" aria-label="Close view of a red bull"></div><h3>Herd Sires</h3><p>Elite genetics with proven marbling &amp;<br>calving ease. Semen available.</p><a class="btn" style="left:80px;top:335px;width:126px;height:32px;font-size:15px">• Read More •</a></div>
<div class="card" style="left:457px"><div class="photo" style="background:linear-gradient(180deg,#8aa86a,#6f8f42 55%,#b0b2ae)" role="img" aria-label="Rancher pouring milk into a can beside grazing cows"></div><h3>Foundation Dams</h3><p>Deep-pedigreed females with superior<br>milk, fertility &amp; structure.</p><a class="btn" style="left:80px;top:335px;width:126px;height:32px;font-size:15px">• Read More •</a></div>
<div class="card" style="left:773px"><div class="photo" style="background:linear-gradient(135deg,#5aa0d0,#c8ccd0 50%,#6a6660)" role="img" aria-label="Technician handling a frozen genetics storage tank"></div><h3>Frozen Genetics</h3><p>Semen, embryos, and custom collections —<br>shipped worldwide.</p><a class="btn" style="left:80px;top:335px;width:126px;height:32px;font-size:15px">• Read More •</a></div>

<div class="abs field-band" role="img" aria-label="Herd of cattle grazing on a green pasture"></div>

<!-- inquiry -->
<h2 class="abs heading" style="left:0;width:1200px;text-align:center;top:2570px;font-size:43px">Inquiry Now</h2>
<div class="wire" style="left:568px;top:2628px"></div>
<form>
  <label class="input" style="left:293px;top:2670px;width:299px;height:53px"><svg width="14" height="14" viewBox="0 0 14 14" fill="none" stroke="#9a8f86"><circle cx="7" cy="4" r="3"/><path d="M1 13c0-3 3-5 6-5s6 2 6 5"/></svg><span class="sep"></span>First Name</label>
  <label class="input" style="left:608px;top:2670px;width:300px;height:53px"><svg width="14" height="14" viewBox="0 0 14 14" fill="none" stroke="#9a8f86"><circle cx="7" cy="4" r="3"/><path d="M1 13c0-3 3-5 6-5s6 2 6 5"/></svg><span class="sep"></span>Last Name</label>
  <label class="input" style="left:293px;top:2738px;width:299px;height:53px"><svg width="14" height="12" viewBox="0 0 14 12" fill="none" stroke="#9a8f86"><rect x="1" y="1" width="12" height="10"/><path d="M1 1l6 5 6-5"/></svg><span class="sep"></span>Your Email</label>
  <label class="input" style="left:608px;top:2738px;width:300px;height:53px"><svg width="14" height="14" viewBox="0 0 14 14" fill="none" stroke="#9a8f86"><path d="M3 1l3 3-2 2c1 2 2 3 4 4l2-2 3 3-2 2C6 13 1 8 1 3z"/></svg><span class="sep"></span>Phone</label>
  <label class="input top" style="left:293px;top:2806px;width:615px;height:107px"><svg width="14" height="14" viewBox="0 0 14 14" fill="none" stroke="#9a8f86"><circle cx="7" cy="7" r="6"/></svg><span class="sep"></span>Ranch Inquiry, Cattle, Property...</label>
  <a class="btn" style="left:506px;top:2948px;width:146px;height:36px;font-size:17px">• Submit Now •</a>
</form>

<!-- trail list -->
<section class="abs trail"></section>
<h2 class="abs heading" style="left:0;width:1200px;text-align:center;top:3150px;font-size:43px;color:var(--white)">Join the Trail List</h2>
<div class="wire" style="left:568px;top:3207px;background:var(--white)"></div>
<label class="input" style="left:154px;top:3240px;width:244px;height:53px"><svg width="14" height="14" viewBox="0 0 14 14" fill="none" stroke="#9a8f86"><circle cx="7" cy="4" r="3"/><path d="M1 13c0-3 3-5 6-5s6 2 6 5"/></svg><span class="sep"></span>Full Name</label>
<label class="input" style="left:412px;top:3240px;width:243px;height:53px"><svg width="14" height="12" viewBox="0 0 14 12" fill="none" stroke="#9a8f86"><rect x="1" y="1" width="12" height="10"/><path d="M1 1l6 5 6-5"/></svg><span class="sep"></span>Your Email</label>
<label class="input" style="left:669px;top:3240px;width:244px;height:53px"><svg width="12" height="15" viewBox="0 0 12 15" fill="none" stroke="#9a8f86"><path d="M6 14s5-5 5-8.5A5 5 0 0 0 1 5.5C1 9 6 14 6 14z"/><circle cx="6" cy="5.5" r="1.8"/></svg><span class="sep"></span>Street, City, Zip</label>
<a class="abs" style="left:927px;top:3240px;width:120px;height:53px;background:var(--rust);border-radius:3px;display:flex;align-items:center;justify-content:center;font-family:'Bebas Neue',sans-serif;font-size:21px;letter-spacing:1.5px;color:var(--white)">Sign Up</a>

<!-- footer -->
<footer class="abs footer">
  <div class="abs" style="left:141px;top:72px;width:190px;font-family:'Bebas Neue',sans-serif;font-size:28px;line-height:30px;color:var(--white)">Birchwell Hollow<br>Cattle Company</div>
  <p class="abs" style="left:141px;top:207px;width:230px;font-size:11px;line-height:18px">Nestled in the rolling hills of Kentucky, we've spent four decades perfecting the Angus breed.</p>
  <div class="abs" style="left:455px;top:70px"><h4>Quick Links</h4>
    <div class="links" style="margin-top:4px"><a>Home</a><a>About Us</a><a>Sires</a><a>Dams</a><a>Frozen Genetics</a><a>For Sale</a><a>Contact Us</a></div></div>
  <div class="abs contact" style="left:666px;top:70px;width:230px"><h4>Contact Details</h4>
    <div style="display:flex;gap:8px;margin-top:12px"><svg width="12" height="15" viewBox="0 0 12 15" fill="#fff"><path d="M6 14s5-5 5-8.5A5 5 0 0 0 1 5.5C1 9 6 14 6 14z"/></svg><span>410 Fence Line Rd.<br>Prairie Town, AR 12345</span></div>
    <div style="display:flex;gap:8px;margin-top:12px"><svg width="12" height="12" viewBox="0 0 14 14" fill="#fff"><path d="M3 1l3 3-2 2c1 2 2 3 4 4l2-2 3 3-2 2C6 13 1 8 1 3z"/></svg><span>Phone:<br>403-555-0148</span></div>
    <div style="display:flex;gap:8px;margin-top:12px"><svg width="13" height="11" viewBox="0 0 14 12" fill="#fff"><rect x="1" y="1" width="12" height="10"/></svg><span>Email<br>info@birchwellhollow.com</span></div>
  </div>
  <div class="abs social" style="left:956px;top:70px"><h4>Social Media</h4>
    <div style="margin-top:8px"><i></i>Ranch Feed</div><div><i></i>Video Barn</div><div><i></i>Trade Network</div><div><i></i>Photo Stream</div></div>
  <div class="abs" style="left:141px;top:347px;width:918px;height:1px;background:#4a3e36"></div>
  <p class="abs" style="left:0;width:1200px;top:362px;text-align:center;font-size:12px">© 2026 Birchwell Hollow. All Rights Reserved.</p>
</footer>

</body>
</html>
```